Yoga Workshop - Yoga Practice information flyer

I am a yoga teacher who will be presenting a workshop on yoga for sleep and need a brochure for my clients which outlines a practice that I give them so they can do the practice at home. Ideally I would like a brochure that is a single A3 size of paper in size that folds in half to an A4 booklet with the entire practice on the centre section to make it easy for people to do the practice at home with just one open page in front of them:
* Front page detailing "Yoga for Sleep Workshop" and "Restorative Yoga Practice"
* Centre contains the information on the practice contained in the attached word document. The practice consists of 5 postures, so there needs to be five separate sections which have the pictures of the postures (attached in uploaded files) and the wording contained in the attached word document. All pictures uploaded need to be included in the flyer as each posture has different pictures demonstrating the posture using yoga props or using things people have at home
* Back page containing a picture of myself (picture uploaded in files) with some information about me (contained in the attached word document) and my website www.calmdrift.com.au

I also need this flyer to be able to printed on 2 double sided A4 sheets of paper so will require 2 x pdf file versions. Importantly, for the centre section of the flyer, the design needs to ensure if it is printed on A4 paper, the wording and pictures for each of the postures are not separated over two pages

Target Market(s)

Existing clients

Requirements
Must have
• Detailed in project description
Nice to have
• The word document also contains some quotes. These do not need to be included in the flyer. If there is room and there is room for one or two of those please include where it would look good
Should not have
• Stock pictures of people in yoga postures which a normal everyday person could not get into

```html
<!DOCTYPE html>
<html lang="en">
<head>
<meta charset="utf-8">
<title>Yoga for Sleep Workshop – Brochure</title>
<link rel="stylesheet" href="https://fonts.googleapis.com/css2?family=Montserrat:ital,wght@0,400;0,600;0,700;1,400;1,700&family=Roboto+Condensed:ital,wght@1,800&display=swap">
<style>
  :root {
    --navy: #1c2b45;
    --navy-deep: #15223a;
    --navy-band: #263b5e;
    --terracotta: #d7936f;
    --orange: #d9764a;
    --cream: #f4f1ea;
    --paper: #f7f6f3;
    --white: #ffffff;
    --stage: #8f8f8f;
    --ink: #1e2c48;
    --mat: #2a7cc4;
  }
  * { box-sizing: border-box; margin: 0; padding: 0; }
  html, body { width: 857px; height: 1200px; overflow: hidden; }
  body {
    background: var(--stage);
    font-family: "Montserrat", sans-serif;
    position: relative;
  }
  .spread {
    position: absolute;
    left: 18px;
    width: 820px;
    height: 580px;
    overflow: hidden;
    box-shadow: 0 6px 18px rgba(0,0,0,.25);
  }
  .spread--outer { top: 13px; }
  .spread--inner { top: 607px; background: var(--navy); }
  .page { position: absolute; top: 0; width: 410px; height: 580px; overflow: hidden; }
  .page--left { left: 0; }
  .page--right { left: 410px; }

  /* Back page */
  .back { background: linear-gradient(160deg, var(--navy) 0%, var(--navy-deep) 100%); color: var(--white); text-align: center; }
  .about__title { margin-top: 46px; color: var(--orange); font-weight: 700; font-style: italic; font-size: 16px; }
  .about__text { width: 330px; margin: 12px auto 0; font-size: 7.2px; line-height: 1.55; font-style: italic; }
  .quote { margin: 22px auto 0; width: 300px; }
  .quote__mark { color: var(--orange); font-size: 26px; line-height: 14px; font-weight: 700; height: 14px; }
  .quote__text { font-size: 8px; line-height: 1.5; font-style: italic; margin-top: 6px; }
  .back__web { position: absolute; left: 40px; bottom: 40px; font-size: 14px; letter-spacing: .5px; }

  /* Front page */
  .front { background: var(--terracotta); }
  .front__head { position: absolute; top: 0; left: 0; width: 410px; height: 128px; background: var(--white); text-align: center; }
  .brand { margin-top: 40px; display: flex; align-items: center; justify-content: center; gap: 10px; }
  .brand__dot { width: 26px; height: 26px; border-radius: 50%; border: 2px solid var(--orange); }
  .brand__name { font-weight: 700; font-size: 22px; color: var(--ink); }
  .brand__tagline { margin-top: 8px; font-size: 8px; letter-spacing: 2px; color: var(--ink); }
  .front__band { position: absolute; left: 0; bottom: 0; width: 410px; height: 150px; background: var(--navy-band); }
  .front__photo { position: absolute; left: 0; top: 0; }
  .front__title {
    position: absolute; left: 30px; bottom: 40px;
    font-family: "Roboto Condensed", sans-serif; font-weight: 800; font-style: italic;
    color: var(--white); font-size: 25px; line-height: 1.1; text-transform: uppercase;
  }

  /* Inner spread */
  .inner__bg { position: absolute; left: 0; top: 0; }
  .fold { position: absolute; left: 409px; top: 0; width: 2px; height: 580px; background: rgba(0,0,0,.08); }
  .pose-photo { position: absolute; border-radius: 2px; }
  .intro { position: absolute; left: 200px; top: 36px; width: 195px; font-size: 6.6px; line-height: 1.5; color: var(--ink); text-align: right; }
  .posture { position: absolute; color: var(--ink); font-size: 6.6px; line-height: 1.5; }
  .posture__tag {
    display: inline-block; background: var(--orange); color: var(--white);
    font-weight: 700; font-size: 8px; letter-spacing: .5px;
    padding: 2px 12px 2px 8px; border-radius: 0 10px 10px 0; margin-bottom: 4px;
  }
  .posture__name { font-weight: 700; font-size: 8px; margin-bottom: 2px; }
  .posture p { margin-top: 3px; }
  .posture b { font-weight: 700; }
  .inner__web { position: absolute; left: 250px; top: 520px; font-size: 8px; font-weight: 600; color: var(--ink); }
</style>
</head>
<body>

<section class="spread spread--outer">
  <article class="page page--left back">
    <h2 class="about__title">About the teacher...</h2>
    <p class="about__text">Mira Holloway is a current serving Navy Officer, Yoga Therapist (C-IAYT) and Restwell Level 2 instructor. Mira's classes are about using the practices and teaching of Yoga to come to the essence of your true self and learning to tap into the internal wisdom which is always present. Mira is dedicated to making the resilience developing practices of Yoga accessible to all Australian Military personnel and their families.</p>
    <div class="quote"><div class="quote__mark">&ldquo;</div><p class="quote__text">"Posture should be steady and comfortable"<br>—Yoga Sutras of Patanjali</p></div>
    <div class="quote"><div class="quote__mark">&ldquo;</div><p class="quote__text">"Tension is who you think you are, Relaxation is who you actually are"</p></div>
    <div class="quote"><div class="quote__mark">&ldquo;</div><p class="quote__text">"Life isn't as serious as the mind makes it out to be"<br>—Elena Marsh</p></div>
    <div class="quote"><div class="quote__mark">&ldquo;</div><p class="quote__text">"Watch your thoughts, they become words<br>Watch your words, they become actions<br>Watch your actions, they become habits<br>Watch your habits, they become character<br>Watch your character, for it becomes your destiny"<br>—Upanishads</p></div>
    <p class="back__web">www.calmdrift.com.au</p>
  </article>

  <article class="page page--right front">
    <header class="front__head">
      <div class="brand"><span class="brand__dot"></span><span class="brand__name">Calm Drift Yoga</span></div>
      <p class="brand__tagline">Be the change you wish to see in the world</p>
    </header>
    <div class="front__band"></div>
    <svg class="front__photo" width="410" height="580" viewBox="0 0 410 580" role="img" aria-label="Photo of the teacher seated cross-legged in meditation on a blanket in a grassy park">
      <defs>
        <linearGradient id="parkTones" x1="0" y1="0" x2="0" y2="1">
          <stop offset="0" stop-color="#6f8f4a"/>
          <stop offset=".55" stop-color="#8c9a62"/>
          <stop offset="1" stop-color="#a89a78"/>
        </linearGradient>
      </defs>
      <path d="M215 150 C245 200 330 260 330 335 A 115 115 0 0 1 100 335 C100 260 185 200 215 150 Z" fill="url(#parkTones)" stroke="var(--cream)" stroke-width="9"/>
    </svg>
    <h1 class="front__title">Yoga for Sleep Workshop and<br>Restorative Yoga Practice</h1>
  </article>
</section>

<section class="spread spread--inner">
  <svg class="inner__bg" width="820" height="580" viewBox="0 0 820 580" aria-hidden="true">
    <ellipse cx="410" cy="290" rx="385" ry="360" fill="var(--paper)" stroke="var(--orange)" stroke-width="5"/>
  </svg>
  <div class="fold"></div>

  <div class="pose-photo" style="left:14px;top:40px;width:110px;height:200px;background:linear-gradient(160deg,var(--mat),#a8523a 60%,#6b4a7a);" role="img" aria-label="Posture 1 photo: supported chest opening lying on a bolster on a blue mat"></div>
  <div class="pose-photo" style="left:14px;top:270px;width:110px;height:200px;background:linear-gradient(160deg,var(--mat),#a8523a 55%,#5d4d7c);" role="img" aria-label="Posture 2 photo: supported bound-angle pose with knees supported"></div>
  <div class="pose-photo" style="left:700px;top:40px;width:110px;height:150px;background:linear-gradient(200deg,#5d4d7c,#a8523a 50%,var(--mat));" role="img" aria-label="Posture 3 photo: elevated legs up the wall on a bolster"></div>
  <div class="pose-photo" style="left:690px;top:215px;width:110px;height:140px;background:linear-gradient(200deg,var(--mat),#a8523a 55%,#c9a27a);" role="img" aria-label="Posture 4 photo: supported child's pose over a bolster"></div>
  <div class="pose-photo" style="left:690px;top:380px;width:120px;height:180px;background:linear-gradient(200deg,var(--mat),#a8523a 45%,#e8e6e2 75%,#5d4d7c);" role="img" aria-label="Posture 5 photo: relaxation pose lying on back with pillow under knees"></div>

  <p class="intro">Use this sequence to relax and unwind at the end of a day or before bed. Settle comfortably into each posture for about 5 minutes. Set a timer to let you know when it is time to change position, and you can also listen to the audio recording from the Yoga for Sleep Workshop. It can also be used in the middle of the night when you can't sleep; you might like to try getting up and resting in any one of these postures for about 5-10 minutes before heading back to bed.</p>

  <div class="posture" style="left:130px;top:130px;width:260px;">
    <span class="posture__tag">POSTURE 1 –</span>
    <p class="posture__name">Supported Chest Opening with Knee Support</p>
    <p><b>PROPS –</b> 2 x bolsters (or towels rolled up lengthways), 1 x cushion for head support (optional)</p>
    <p><b>SET UP NOTES –</b> Position the props in a T-position with one bolster running parallel to the spine and the other under the knees. Position yourself so your lower back is on the floor and the parallel bolster runs from the lower back up to behind the head.</p>
    <p><b>CAUTION –</b> If any lower back pain is experienced adjust the parallel bolster height by using a folded towel or blanket. Do not use any parallel prop if pain continues.</p>
  </div>

  <div class="posture" style="left:130px;top:318px;width:260px;">
    <span class="posture__tag">POSTURE 2 –</span>
    <p class="posture__name">Supported Bound-Angle Pose</p>
    <p><b>PROPS –</b> 1 x bolster (or towel rolled up lengthways), 2 x yoga blocks/bolsters (or pillows), 1 x cushion for head support (optional)</p>
    <p><b>SET UP NOTES –</b> Similar to Posture 1 without the bolster behind the knees. Instead, the soles of the feet are together with knees wide, each knee supported by a block, bolster or pillow.</p>
    <p><b>CAUTION –</b> If any lower back pain is experienced adjust the parallel bolster height by using a folded towel. Do not use any parallel prop if pain continues.</p>
  </div>

  <p class="inner__web">www.calmdrift.com.au</p>

  <div class="posture" style="left:430px;top:60px;width:255px;">
    <span class="posture__tag">POSTURE 3 –</span>
    <p class="posture__name">Elevated Legs-Up-the-Wall Pose</p>
    <p><b>PROPS –</b> 1 x bolster (or towel or blanket densely folded to a width of about 15-30cm), 1 x cushion for head support (optional)</p>
    <p><b>SET UP NOTES –</b> To enter the posture sit at 90 degrees to the wall with the side of your hip about a hand width away from the wall, and the bolster close by. Lie down on your side then roll onto your back and extend feet up the wall. Press into the wall to lift the hips and slide the bolster underneath the sacrum.</p>
    <p><b>CAUTION –</b> If any lower back pain is experienced adjust the height the hips are elevated by using a folded towel or blanket.</p>
  </div>

  <div class="posture" style="left:430px;top:268px;width:245px;">
    <span class="posture__tag">POSTURE 4 –</span>
    <p class="posture__name">Supported Child's Pose</p>
    <p><b>Props –</b> 1-2 x bolsters (or 3-4 bed pillows)</p>
    <p><b>Set up notes –</b> Position bolster or stacked pillows under torso. Rest the head in one direction and remember to turn to the other side half way through the time you spend in this posture.</p>
    <p><b>Caution –</b> If any knee or hip pain is experienced, increase the height of the support under the torso by adding more bolsters, folded blankets or pillows.</p>
  </div>

  <div class="posture" style="left:430px;top:438px;width:250px;">
    <span class="posture__tag">POSTURE 5 –</span>
    <p class="posture__name">Basic Relaxation Posture with Knee Support</p>
    <p><b>Props –</b> 1x bolster (or 1x bed pillow or rolled up towel)</p>
    <p><b>Set up notes –</b> Reclining on back, position bolster or pillows under knees.</p>
  </div>
</section>

</body>
</html>
```